Current website re-design to a updated look and feel.

We currently have a website www.brightlanefreight.com that we want to give an updated look and feel to. We are a logistics company that competes with Pellwick, Dm Harrowgate, Quill but on a smaller scale. We want something fresh and updated. We have two locations one in downtown Chicago, IL and one in Palatine IL. We are a fun group that also gets the job done. We know we need pictures of both locations and possibly a video, but we need fresh design ideas. The 'who we are' page is really the only page that we currently want to keep. The 'what we do' page needs to be completely re-done from a look and feel for sure.

Target Market(s)

Anyone who uses Truck transportation to move their product. Mainly US manufacturers.

Industry/Entity Type

Logistics

Number of Pages Required

5+ page

Font styles to use
Sans Serif

Colors
5c91c4
0355a3
d0dfed

Requirements
Must have
• The new design must entice people to want to do business with us. The design must have locations for pictures and at least one video which we know we will have to provide. Design must be easy to navigate.

```html
<!DOCTYPE html>
<html lang="en">
<head>
<meta charset="utf-8">
<title>Brightlane Freight – Transportation &amp; Logistics</title>
<link rel="stylesheet" href="https://fonts.googleapis.com/css2?family=Open+Sans:wght@400;600;700&family=Montserrat:wght@400;600;700&display=swap">
<style>
:root{
  --blue:#0355a3;
  --blue-mid:#5c91c4;
  --blue-pale:#d0dfed;
  --ink:#333b44;
  --muted:#7a828b;
  --line:#d6dbe0;
  --grey-bg:#f1f2f4;
  --footer-bg:#e9eaec;
  --white:#ffffff;
}
*{box-sizing:border-box;margin:0;padding:0}
html,body{width:1200px;height:2944px;overflow:hidden}
body{font-family:"Open Sans",Arial,sans-serif;color:var(--ink);background:var(--white)}
h1,h2,h3,h4{font-family:"Montserrat",Arial,sans-serif}
a{color:inherit;text-decoration:none}

/* header */
.site-header{height:72px;display:flex;align-items:center;justify-content:space-between;padding:0 120px}
.brand{display:flex;align-items:center;gap:10px;font-family:"Montserrat",sans-serif;font-weight:700;font-size:26px;color:var(--blue)}
.brand-mark{width:22px;height:22px;background:var(--blue-mid)}
.main-nav{display:flex;align-items:center;gap:30px;font-size:14px;color:var(--ink)}
.btn-login{background:var(--blue);color:var(--white);padding:8px 22px;font-size:13px}

/* hero */
.hero{position:relative;height:568px;background:linear-gradient(180deg,#6a6b70 0%,#4a4d55 45%,#2f3239 100%);color:var(--white);text-align:center}
.hero-media{position:absolute;inset:0}
.hero-content{position:relative;padding-top:190px}
.play-btn{display:block;margin:0 auto 52px}
.hero h1{font-size:42px;font-weight:700;letter-spacing:2px}
.hero-sub{font-family:"Montserrat",sans-serif;font-size:24px;font-weight:600;letter-spacing:2px;margin-top:8px;text-transform:uppercase}

/* welcome */
.welcome{height:432px;background:var(--grey-bg);display:flex;align-items:center;padding:0 120px;gap:80px}
.welcome-visual{width:360px;height:300px;background:linear-gradient(160deg,#e4cf9e,#c9a35a 60%,#dcc34a);border-radius:4px}
.welcome-text{width:520px}
.welcome h2{font-size:46px;font-weight:400;color:var(--ink);margin-bottom:14px}
.welcome p{font-size:14px;line-height:1.6;color:var(--muted);margin-bottom:24px}
.btn{display:inline-block;background:var(--blue);color:var(--white);font-size:12px;font-weight:600;padding:9px 20px;text-transform:uppercase}

/* why */
.why{height:368px;background:linear-gradient(120deg,var(--blue) 0%,#1765b0 55%,var(--blue-mid) 100%);display:flex;align-items:center;padding:0 128px;gap:100px;color:var(--white)}
.why-text{width:380px}
.why h2{font-size:34px;font-weight:600;letter-spacing:1px;margin-bottom:18px}
.why p{font-size:13px;line-height:1.65;color:var(--blue-pale);margin-bottom:22px}
.btn-outline{background:transparent;border:1px solid var(--white)}
.service-grid{display:grid;grid-template-columns:232px 232px;grid-template-rows:140px 140px;gap:2px;background:rgba(255,255,255,.5)}
.service-tile{display:flex;flex-direction:column;align-items:center;justify-content:center;gap:12px;background:var(--blue);font-size:15px;color:var(--white)}
.service-tile.is-active{background:var(--white);color:var(--blue)}

/* feature cards */
.features{height:600px;display:flex;justify-content:center;gap:24px;padding-top:100px}
.feature-card{width:304px;text-align:center}
.feature-img{height:192px;margin-bottom:24px}
.feature-card h3{font-family:"Open Sans",sans-serif;font-size:26px;font-weight:600;color:var(--ink);margin-bottom:8px}
.feature-card p{font-size:12px;color:var(--muted);line-height:1.5;margin:0 22px 16px}
.btn-ghost{display:inline-block;border:1px solid var(--blue);color:var(--blue);font-size:11px;font-weight:600;padding:7px 18px;text-transform:uppercase}

/* contact */
.contact{position:relative;height:360px;background:linear-gradient(180deg,#3c5468 0%,#2c3e4f 50%,#6a4b3b 100%);color:var(--white);text-align:center}
.contact-bg{position:absolute;inset:0}
.contact-inner{position:relative;padding-top:36px;width:760px;margin:0 auto}
.contact h2{font-size:34px;font-weight:400;letter-spacing:2px;margin-bottom:26px}
.contact-form{display:grid;grid-template-columns:1fr 1fr;column-gap:40px;row-gap:14px;text-align:left}
.field{border-bottom:1px solid rgba(255,255,255,.8);padding:6px 2px;font-size:14px;color:var(--white);background:rgba(255,255,255,.08)}
.field.full{grid-column:1/3;height:40px}
.btn-submit{grid-column:1/3;justify-self:center;background:var(--blue);color:var(--white);font-family:"Open Sans",Arial,sans-serif;font-size:16px;font-weight:600;padding:12px 42px;margin-top:10px;border:0}

/* partners */
.partners{height:160px;display:flex;align-items:center;justify-content:center;gap:34px}
.partner-badge{height:64px;background:var(--blue-pale)}
.partner-badge.round{border-radius:50%;width:64px}
.arrow{color:var(--muted)}

/* footer */
.site-footer{height:280px;background:var(--footer-bg);display:flex;padding:60px 120px 0;gap:60px}
.footer-col h4{font-size:18px;font-weight:600;color:var(--blue);margin-bottom:10px;text-transform:uppercase}
.footer-col ul{list-style:none;font-size:13px;line-height:1.65;color:var(--muted)}
.footer-col{width:200px}
.footer-aside{margin-left:auto;display:flex;gap:22px;align-items:flex-start}
.award{width:56px;height:80px;background:var(--blue-pale)}
.award-box{width:130px;height:70px;border:1px solid var(--line);background:var(--white)}
.social{display:flex;gap:8px;margin-top:10px}
.social span{width:26px;height:26px;border-radius:50%;border:1px solid var(--blue)}
.copyright{height:64px;background:#dfe0e2;display:flex;align-items:center;justify-content:center;font-size:12px;color:var(--muted)}
</style>
</head>
<body>

<header class="site-header">
  <a class="brand" href="#"><span class="brand-mark"></span>Brightlane Freight</a>
  <nav class="main-nav">
    <a href="#">What We Do</a>
    <a href="#">How We Do It</a>
    <a href="#">Who We Are</a>
    <a href="#">Tracking</a>
    <a href="#">Contact</a>
    <a class="btn-login" href="#">Log In</a>
  </nav>
</header>

<section class="hero">
  <div class="hero-media" role="img" aria-label="Video still of a city skyline and highway with trucks at sunset"></div>
  <div class="hero-content">
    <svg class="play-btn" width="72" height="72" viewBox="0 0 72 72" aria-label="Play video">
      <circle cx="36" cy="36" r="34" fill="none" stroke="#fff" stroke-width="3"/>
      <path d="M29 23 L51 36 L29 49 Z" fill="#fff"/>
    </svg>
    <h1>TRANSPORTATION &amp; LOGISTICS</h1>
    <p class="hero-sub">Mauris Vellacus Felis Vestibulum</p>
  </div>
</section>

<section class="welcome">
  <div class="welcome-visual" role="img" aria-label="Forklift carrying a stack of cardboard boxes on a pallet"></div>
  <div class="welcome-text">
    <h2>Welcome</h2>
    <p>Brightlane Freight welcomes you to our growing family of clients. We have over 20 years of experience in helping people solve their logistics needs from coast to coast. We also provide friendly, exceptional service that makes it easy to do business with us. Give us a call today and experience the difference for yourself.</p>
    <a class="btn" href="#">Learn More</a>
  </div>
</section>

<section class="why">
  <div class="why-text">
    <h2>WHY WE ARE</h2>
    <p>Brightlane Freight is one of the premier third-party logistics solutions in North America. We will become premier by providing superior customer service, efficient and cost-effective warehousing and distribution solutions. The decisions we make today for hiring, training, technology, strategic services and customer satisfaction are based on this vision.</p>
    <a class="btn btn-outline" href="#">Learn More</a>
  </div>
  <div class="service-grid">
    <div class="service-tile is-active">
      <svg width="64" height="40" viewBox="0 0 64 40" fill="none" stroke="currentColor" stroke-width="2.5"><rect x="2" y="6" width="38" height="22"/><path d="M40 12h12l8 8v8H40z"/><circle cx="14" cy="32" r="5" fill="#fff"/><circle cx="50" cy="32" r="5" fill="#fff"/></svg>
      Freight Management
    </div>
    <div class="service-tile">
      <svg width="64" height="40" viewBox="0 0 64 40" fill="none" stroke="currentColor" stroke-width="2.5"><rect x="2" y="6" width="38" height="22"/><path d="M40 12h12l8 8v8H40z"/><circle cx="14" cy="32" r="5"/><circle cx="50" cy="32" r="5"/></svg>
      Transportation
    </div>
    <div class="service-tile">
      <svg width="56" height="44" viewBox="0 0 56 44" fill="none" stroke="currentColor" stroke-width="2.5"><path d="M2 16 L28 3 L54 16 V42 H2 Z"/><rect x="14" y="24" width="28" height="18"/><path d="M14 30h28M14 36h28"/></svg>
      Warehouse
    </div>
    <div class="service-tile">
      <svg width="50" height="44" viewBox="0 0 50 44" fill="none" stroke="currentColor" stroke-width="2.5"><rect x="3" y="3" width="20" height="18"/><rect x="27" y="3" width="20" height="18"/><rect x="15" y="23" width="20" height="18"/></svg>
      Distribution
    </div>
  </div>
</section>

<section class="features">
  <article class="feature-card">
    <div class="feature-img" role="img" aria-label="Container ship loaded with cargo on the sea" style="background:linear-gradient(180deg,#b9d3ea 0%,#7aa8cf 55%,#2f6a9c 100%)"></div>
    <h3>How We Work</h3>
    <p>Learn how our team plans every load from pickup to delivery.</p>
    <a class="btn-ghost" href="#">Learn More</a>
  </article>
  <article class="feature-card">
    <div class="feature-img" role="img" aria-label="Person checking shipment status on a tablet" style="background:linear-gradient(160deg,#d9dde2 0%,#9aa4ae 60%,#5e6a76 100%)"></div>
    <h3>Tracking</h3>
    <p>Follow your shipment in real time with clear status updates.</p>
    <a class="btn-ghost" href="#">Learn More</a>
  </article>
  <article class="feature-card">
    <div class="feature-img" role="img" aria-label="Warehouse worker in a safety vest among stacked shelves" style="background:linear-gradient(160deg,#e6dcc4 0%,#b8a478 55%,#d6c23e 100%)"></div>
    <h3>Who We Are</h3>
    <p>Meet the friendly crew that keeps your freight moving daily.</p>
    <a class="btn-ghost" href="#">Learn More</a>
  </article>
</section>

<section class="contact">
  <div class="contact-bg" role="img" aria-label="Shipping port with stacked cargo containers and cranes"></div>
  <div class="contact-inner">
    <h2>CONTACT US</h2>
    <form class="contact-form">
      <div class="field">First Name</div>
      <div class="field">Last Name</div>
      <div class="field">Email</div>
      <div class="field">Phone</div>
      <div class="field full">Message</div>
      <button class="btn-submit" type="button">SUBMIT</button>
    </form>
  </div>
</section>

<section class="partners" aria-label="Partners and awards">
  <svg class="arrow" width="14" height="24" viewBox="0 0 14 24"><path d="M12 2 L2 12 L12 22" fill="none" stroke="currentColor" stroke-width="2"/></svg>
  <span class="partner-badge" style="width:90px"></span>
  <span class="partner-badge" style="width:130px"></span>
  <span class="partner-badge" style="width:110px"></span>
  <span class="partner-badge" style="width:90px"></span>
  <span class="partner-badge round"></span>
  <span class="partner-badge round"></span>
  <span class="partner-badge round"></span>
  <svg class="arrow" width="14" height="24" viewBox="0 0 14 24"><path d="M2 2 L12 12 L2 22" fill="none" stroke="currentColor" stroke-width="2"/></svg>
</section>

<footer class="site-footer">
  <div class="footer-col">
    <h4>Company</h4>
    <ul><li>About Us</li><li>Our Mission</li><li>What We Do</li><li>How We're Working</li></ul>
  </div>
  <div class="footer-col">
    <h4>Our Services</h4>
    <ul><li>Transportation</li><li>Carriers</li><li>Warehouse &amp; Distribution</li><li>Freight Management</li></ul>
  </div>
  <div class="footer-col" style="width:240px">
    <h4>Contact Us</h4>
    <ul><li>118 Orchard Row Unit 7</li><li>Marlow Falls, IL 60999</li><li>555.201.0143</li><li>555.201.0188</li><li>info@brightlanefreight.com</li></ul>
  </div>
  <div class="footer-aside">
    <span class="award"></span>
    <div>
      <div class="award-box"></div>
      <div class="social"><span></span><span></span><span></span><span></span></div>
    </div>
  </div>
</footer>
<div class="copyright">© 2017 Company Name. All rights reserved.</div>

</body>
</html>
```